Beauty Therapy Web Design

I need a web page design for a small beauty therapy clinic, the owner is currently the only beauty therapist working there.
We require the following pages:
Home
About
Treatments
Nails
Courses
Contact
I will attach the clinics business card, treatment menu and signage so that you get a feeling for the branding colours etc.
This is the first website for the beauty therapist, she would like to attract new clients and also tourists that come in on the cruise ships. The thing that sets her apart from other clinics is that she welcomes texting for appointments.
I have selected refundable because I have never done this before so I don't know what to expect, I have the full intention of going through with it as long as I get a good design.
Feel free to ask for further information
Reason: Project extended as I am away for work and am unable to meet with the owner.
Target Market(s)
Females 18 to 50
Industry/Entity Type
Business
Look and feel

```html
<!DOCTYPE html>
<html lang="en">
<head>
<meta charset="utf-8">
<title>Lumina Beauty Therapy – Contact</title>
<link href="https://fonts.googleapis.com/css2?family=EB+Garamond:ital,wght@0,400;0,500;1,400;1,500&family=Source+Sans+3:wght@400;600&display=swap" rel="stylesheet">
<style>
:root{
  --lilac:#a98ade;
  --lilac-dark:#8d6bd6;
  --lilac-text:#9b7bdc;
  --plum:#3a1670;
  --grey-text:#6d6d6d;
  --grey-title:#8a8a8a;
  --line:#cfcfcf;
  --field:#bdbdbd;
  --white:#ffffff;
}
*{margin:0;padding:0;box-sizing:border-box}
html,body{width:1200px;height:899px;overflow:hidden;background:var(--white)}
body{position:relative;font-family:"Source Sans 3",sans-serif;color:var(--grey-text)}
.abs{position:absolute}
.top-band{left:10px;top:0;width:1180px;height:6px;background:var(--lilac);border-radius:0 0 6px 6px}
.brand-mark{left:192px;top:46px;width:16px;height:16px;background:var(--lilac)}
.brand-name{left:218px;top:34px;font-family:"EB Garamond",serif;font-size:32px;line-height:1;color:var(--lilac-dark);font-weight:500;white-space:nowrap}
.call{left:658px;top:12px;font-family:"EB Garamond",serif;font-style:italic;font-size:27px;color:var(--lilac-text)}
.social{top:5px;width:39px;height:39px;border-radius:5px;background:linear-gradient(#fbfbfb,#e6e6e6);border:1px solid #d2d2d2;box-shadow:0 1px 2px rgba(0,0,0,.15)}
.main-nav a,.foot-nav a{position:absolute;font-family:"EB Garamond",serif;font-style:italic;text-decoration:none;white-space:nowrap}
.main-nav a{top:82px;font-size:18px;color:var(--lilac-dark)}
.nav-marker{left:978px;top:107px;width:65px;height:4px;border-radius:3px;background:var(--lilac)}
.page-title{left:201px;top:162px;font-family:"EB Garamond",serif;font-style:italic;font-size:27px;color:#111;border-bottom:1.5px solid #111;line-height:1.05;font-weight:400}
.form-title{left:231px;top:242px;font-size:17px;color:var(--grey-title)}
.label{left:231px;font-size:12px;color:var(--grey-text)}
.field{left:231px;width:226px;height:19px;border:1px solid var(--field);background:var(--white)}
.submit{left:268px;top:513px;width:142px;height:22px;border-radius:4px;background:linear-gradient(var(--lilac),var(--lilac-dark));color:var(--white);font-size:12.5px;font-weight:600;text-align:center;line-height:22px}
.divider{left:608px;top:251px;width:1px;height:289px;background:var(--line)}
.map{left:629px;top:267px;width:233px;height:233px;border:1px solid #c9c9c9;background:linear-gradient(135deg,#ece8df,#e3ded3 60%,#efe9c9)}
.details-title{left:929px;top:378px;font-size:17px;color:#666}
.detail{left:897px;font-size:11px;color:#555}
.foot-bar{left:10px;top:588px;width:1180px;height:33px;border-radius:10px;background:var(--lilac);box-shadow:0 12px 14px -10px rgba(0,0,0,.18)}
.foot-nav a{top:594px;font-size:18px;color:var(--plum)}
.copyright{left:0;width:1200px;top:636px;text-align:center;font-family:"EB Garamond",serif;font-style:italic;font-size:14px;color:var(--plum)}
</style>
</head>
<body>
<div class="abs top-band"></div>

<header>
  <div class="abs brand-mark"></div>
  <div class="abs brand-name">Lumina Beauty Therapy</div>

  <div class="abs call">Call Us 555 214 7730</div>
  <div class="abs social" style="left:902px" aria-label="Social link"></div>
  <div class="abs social" style="left:948px" aria-label="Social link"></div>
  <div class="abs social" style="left:992px" aria-label="Social link"></div>

  <nav class="main-nav">
    <a href="#" style="left:538px">Home</a>
    <a href="#" style="left:618px">About</a>
    <a href="#" style="left:699px">Treatments</a>
    <a href="#" style="left:814px">Nails</a>
    <a href="#" style="left:890px">Courses</a>
    <a href="#" style="left:982px">Contact</a>
  </nav>
  <div class="abs nav-marker"></div>
</header>

<main>
  <h1 class="abs page-title">Contact Us</h1>

  <section class="enquiry">
    <div class="abs form-title">Kindly post your valuable Suggestions &amp; Query</div>
    <div class="abs label" style="top:281px">Enter your Name</div>
    <div class="abs field" style="top:299px"></div>
    <div class="abs label" style="top:325px">Enter your Email</div>
    <div class="abs field" style="top:345px"></div>
    <div class="abs label" style="top:370px">Enter your Phone Number</div>
    <div class="abs field" style="top:391px"></div>
    <div class="abs label" style="top:414px">Add Your Comments Here:</div>
    <div class="abs field" style="top:430px;height:44px"></div>
    <div class="abs submit">Submit Query</div>
  </section>

  <div class="abs divider"></div>

  <div class="abs map" role="img" aria-label="Street map showing the clinic location"></div>

  <section class="contact-details">
    <svg class="abs" style="left:894px;top:378px" width="24" height="24" viewBox="0 0 24 24" aria-hidden="true">
      <rect width="24" height="24" rx="4" fill="#dcdcdc"/>
      <path d="M9 5 Q6 6 6 9 Q7 16 14 19 Q17 19 18 16 L15 14 L13 15 Q10 13 9 10 L10 8 Z" fill="#fff"/>
    </svg>
    <div class="abs details-title">Contact Details</div>
    <div class="abs detail" style="top:416px">#12 Willow Lane, Bayview,</div>
    <div class="abs detail" style="top:438px">Phone: +1 555 301 4422</div>
    <div class="abs detail" style="top:460px">Tollfree: (800) 555 0190</div>
    <div class="abs detail" style="top:482px">E-mail: hello@luminaspa.com</div>
  </section>
</main>

<footer>
  <div class="abs foot-bar"></div>
  <nav class="foot-nav">
    <a href="#" style="left:367px">Home</a>
    <a href="#" style="left:442px">About</a>
    <a href="#" style="left:518px">Treatments</a>
    <a href="#" style="left:625px">Nails</a>
    <a href="#" style="left:695px">Courses</a>
    <a href="#" style="left:781px">Contact</a>
  </nav>
  <div class="abs copyright">Copyright © 2012.www.luminabeautytherapy.com</div>
</footer>
</body>
</html>
```